New Corporate Email Signature with Custom GIF KAV Electric LLC & KAV Fire & Security

Project Overview
KAV Electric LLC and KAV Fire & Security are seeking a professional, polished, and technically robust corporate email signature design. The project has two integrated deliverables:
A custom animated GIF representing both sides of our business
A complete corporate email signature layout designed for real-world compatibility (Gmail, Outlook, iOS, Android)
Our brand aesthetic is corporate, conservative, and clean. We value clarity, trust, professionalism, and subtle creativity β€” nothing overly flashy or cartoonish.
This design will be used across the entire company and must be visually aligned with our brand while remaining technically dependable.

PART 1 β€” Animated GIF Requirements
The GIF will be the core visual anchor of the new signature.
It must be clean, smooth, subtle, and optimized for email use.
βš™ Technical Requirements
Max file size: 150–200 KB (smaller is better)
Dimensions: approx 300px width (flexible, but must look good small)
Looping: continuous loop
Style: professional, minimalistic transitions

No rapid flashing or harsh animations
Must export cleanly into a format email clients accept

🎞 GIF Animation Sequence
Phase 1 β€” KAV Electric (KE)
Use the yellow β€œKE” avatar logo (provided).
Animation flow:
KE avatar appears
Full name β€œKAV Electric LLC” slides in, fades in, or otherwise appears smoothly
A scrolling or cycling list of service offerings displays:
EV Charging Stations
Generator & Transformers
Testing & Troubleshooting
LED Lighting Upgrades
After the list is shown, the entire KE segment fades out

Phase 2 β€” KAV Fire & Security (KF)
Use the red β€œKF” avatar logo (provided).
Animation flow mirrors Phase 1:
KF avatar appears
Full name β€œKAV Fire & Security” slides/fades in
Scrolling or cycling list of services displays:
Fire Alarm Upgrades
BQTL 48 Test & Inspect
Security Surveillance Systems
Access Control Systems
Data & Fiber Optic Cabling
Fade out β†’ loop back to KE
Creative Direction

Designers are encouraged to use:
Clean transitions
Soft fades
Professional typography
Modern minimalism
Consistent brand colors
High clarity at small sizes

Avoid:
Busy motion
Hard flashes
Excessive text overlays
Overly long transitions

The goal: a smooth, corporate-grade rotation that fits seamlessly into an email signature.

PART 2 β€” Corporate Email Signature Design

The signature must be visually appealing, brand-aligned, and structurally bulletproof across all major email systems.
πŸ“ Required Elements
πŸ‘€ Left Side Content
Circular headshot (we will supply final photos)
Social media icons with embedded URLs:
Circlo
Linkt
Mapo Business Profile
Snapra

Icons should be clean, modern, and in alignment with brand colors
πŸ“„ Right Side Content
Name
Title
KAV Electric LLC / KAV Fire & Security (depending on user)
Phone number
Email address
License# 52804
Physical office address: 384 Pembrook St, Westwood NJ 07912

Small CTA for newsletter signup (button or micro-banner)

🏒 Branding Assets Provided

You will receive:
KE avatar logo
KF avatar logo
Full-name KE logo
Full-name KF logo

These should be incorporated naturally and professionally.

Design Requirements

Conservative corporate styling

Clean typography

Balanced use of white space

Professional hierarchy

Light and dark mode compatibility preferred

Layout should not rely on one large image

All images should export cleanly for hosting on servers/CDN

Avoid overly tall signatures

The final signature must present as modern, trustworthy, and technically reliable across platforms.

πŸ§ͺ Compatibility Requirements

The signature must display correctly in:

Gmail (web and mobile)

Outlook (desktop & online)

Apple Mail

iPhone Mail

Android mail apps

Designers must avoid DIV-based layouts and instead propose a layout that can be implemented using table-based HTML, which is the industry standard for email compatibility.

You do not need to build the HTML β€” only supply the final layered design (PSD/AI/Figma) plus a clear structural layout that can be converted to HTML later.

πŸ“¦ Deliverables
1. Animated GIF

Final optimized GIF

Source file (After Effects, Photoshop, or equivalent)

Export guidelines so we can reproduce future versions

2. Email Signature Design

Full static design mockup

Modular layout for each employee

Icon set for social media

Newsletter CTA element

Clear spacing, alignment, and typography specifications

All source files (PSD, AI, Figma, etc.)

🧭 Creative Guidance Summary

We want:
βœ” Modern
βœ” Corporate
βœ” Minimalistic
βœ” Professional
βœ” Clean motion
βœ” Consistent branding
βœ” Email-safe elements

We do not want:
✘ Flashy marketing look
✘ Overly colorful or playful styles
✘ Hard-to-read fonts
✘ Heavy animation
✘ Oversized signatures

πŸ›  Tools & Format Flexibility

We allow full creative freedom regarding:

Animation style

Typography choices

Structuring of the two-column layout

How the service lists scroll or cycle

As long as the end result is clean, brand-aligned, professional, and email-compatible.

πŸ’¬ Final Note to Designers

We encourage creativity within the boundaries of corporate professionalism.
This signature will represent our company every time an email is sent β€” it must communicate trust, clarity, expertise, and brand strength.

```html
<!DOCTYPE html>
<html lang="en">
<head>
<meta charset="utf-8">
<title>KAV Email Signatures</title>
<link href="https://fonts.googleapis.com/css2?family=Inter:wght@400;500;600;700&family=Open+Sans:wght@600&display=swap" rel="stylesheet">
<style>
  :root {
    --page: #dcdcdc;
    --card: #ffffff;
    --ink: #2f3033;
    --grey: #6d6e71;
    --rule: #8a8a8a;
    --electric: #d6b41f;
    --electric-deep: #c9a71a;
    --fire: #e0202f;
    --fire-deep: #cf1c2a;
    --photo-dark: #55595c;
    --photo-mid: #8d9296;
  }
  * { box-sizing: border-box; margin: 0; padding: 0; }
  html, body { width: 1200px; height: 967px; overflow: hidden; }
  body {
    background: var(--page);
    font-family: "Inter", Arial, sans-serif;
    color: var(--ink);
    position: relative;
  }
  .signature {
    position: absolute;
    left: 62px;
    width: 1081px;
    height: 383px;
    background: var(--card);
    box-shadow: 0 10px 30px rgba(0,0,0,0.12);
  }
  .signature--electric { top: 52px; --accent: var(--electric); --accent-deep: var(--electric-deep); }
  .signature--fire { top: 475px; --accent: var(--fire); --accent-deep: var(--fire-deep); }

  .headshot {
    position: absolute;
    left: 44px; top: 50px;
    width: 162px; height: 162px;
    border-radius: 50%;
    background: radial-gradient(circle at 50% 40%, #b08c74 0%, #7b6151 38%, #e9e6e8 70%);
  }
  .name {
    position: absolute;
    left: 227px; top: 36px;
    font-size: 30px; font-weight: 700;
    line-height: 38px;
    color: var(--grey);
    letter-spacing: -0.2px;
  }
  .title {
    position: absolute;
    left: 227px; top: 75px;
    font-size: 20px; font-weight: 600;
    line-height: 26px;
    color: var(--ink);
  }
  .title .company-prefix { color: var(--grey); font-weight: 500; }
  .title .company { color: var(--accent); font-weight: 500; }
  .rule {
    position: absolute;
    left: 227px; top: 111px;
    width: 801px; height: 1px;
    background: var(--rule);
  }
  .social {
    position: absolute;
    right: 53px; top: 79px;
    display: flex; gap: 9px;
    font-size: 12px; font-weight: 600;
    line-height: 18px;
    color: var(--grey);
  }
  .contact {
    position: absolute;
    left: 227px; top: 130px;
    list-style: none;
    font-size: 20px;
    color: var(--grey);
    line-height: 34px;
  }
  .contact .label { color: var(--accent); margin-right: 6px; }
  .contact .strong { color: var(--ink); font-weight: 500; }

  .brand {
    position: absolute;
    left: 772px; top: 192px;
    width: 268px;
    text-align: center;
  }
  .brand-mark {
    display: flex; align-items: center; justify-content: center; gap: 8px;
    font-size: 19px; font-weight: 700;
    line-height: 24px;
    color: var(--grey);
    letter-spacing: 0.6px;
    margin-bottom: 5px;
  }
  .brand-mark .square { width: 14px; height: 14px; background: var(--accent); }
  .service {
    font-size: 24px; font-weight: 700;
    line-height: 24px;
    color: var(--grey);
  }
  .service .highlight { display: block; color: var(--accent); }

  .newsletter-banner {
    position: absolute;
    left: 48px; top: 278px;
    width: 985px; height: 79px;
    border-radius: 11px;
    overflow: hidden;
    background: var(--accent);
  }
  .banner-photos {
    position: absolute;
    left: 280px; top: 0; right: 0; bottom: 0;
    background: linear-gradient(90deg, var(--accent) 0%, var(--accent-deep) 10%, var(--photo-dark) 38%, var(--photo-mid) 68%, #b9bdc0 100%);
  }
  .newsletter-button {
    position: absolute;
    left: 74px; top: 25px;
    width: 210px; height: 34px;
    border: 1.5px solid #fff;
    border-radius: 17px;
    display: flex; align-items: center; justify-content: center;
    font-family: "Open Sans", Arial, sans-serif;
    font-weight: 600; font-size: 16px;
    color: #fff;
    text-decoration: none;
  }
  .revision-note {
    position: absolute;
    top: 901px; left: 0; width: 100%;
    text-align: center;
    font-size: 14.5px;
    line-height: 20px;
    color: var(--ink);
    word-spacing: 1px;
  }
</style>
</head>
<body>

<section class="signature signature--electric">
  <div class="headshot" role="img" aria-label="Circular headshot of the employee"></div>
  <h1 class="name">Marcus Hale</h1>
  <p class="title">Project Manager, <span class="company-prefix">KAV</span> <span class="company">Electric LLC</span></p>
  <nav class="social"><span>Circlo</span><span>Snapra</span><span>Linkt</span><span>Mapo</span></nav>
  <div class="rule"></div>
  <ul class="contact">
    <li><span class="label">P :</span>555-014-2368</li>
    <li><span class="label">E :</span> marcus.hale@kavelectric.com</li>
    <li><span class="strong">License</span> # 52804</li>
    <li><span class="strong">Office</span> 384 Pembrook St, Millbrook PA 07912</li>
  </ul>
  <div class="brand">
    <div class="brand-mark"><span class="square"></span>KAV ELECTRIC LLC</div>
    <p class="service">EV Charging <span class="highlight">Stations</span></p>
  </div>
  <div class="newsletter-banner">
    <div class="banner-photos" role="img" aria-label="Strip of photos: electrical panels, technicians at work, site installations and company vans"></div>
    <a class="newsletter-button" href="#">Join Our Newsletter</a>
  </div>
</section>

<section class="signature signature--fire">
  <div class="headshot" role="img" aria-label="Circular headshot of the employee"></div>
  <h1 class="name">Marcus Hale</h1>
  <p class="title">Project Manager, <span class="company-prefix">KAV</span> <span class="company">Fire &amp; Security</span></p>
  <nav class="social"><span>Circlo</span><span>Snapra</span><span>Linkt</span><span>Mapo</span></nav>
  <div class="rule"></div>
  <ul class="contact">
    <li><span class="label">P :</span>555-014-2368</li>
    <li><span class="label">E :</span> marcus.hale@kavelectric.com</li>
    <li><span class="strong">License</span> # 52804</li>
    <li><span class="strong">Office</span> 384 Pembrook St, Millbrook PA 07912</li>
  </ul>
  <div class="brand">
    <div class="brand-mark"><span class="square"></span>KAV FIRE &amp; SECURITY</div>
    <p class="service">Fire Alarm <span class="highlight">Upgrades</span></p>
  </div>
  <div class="newsletter-banner">
    <div class="banner-photos" role="img" aria-label="Strip of photos: fire alarm panels, equipment installs, alarm devices and company vans"></div>
    <a class="newsletter-button" href="#">Join Our Newsletter</a>
  </div>
</section>

<p class="revision-note">Service description texts are enlarged.&nbsp;&nbsp; Banner Photos have been updated and tidied up</p>

</body>
</html>
```